Business Card Re-Design/Update

We'd like to update out business cards. I've included our current "Style guide" which has the colour scheme of the organisation in it. I've also included the branding files with logos etc in them.

I've also included a copy of one of our existing cards so that you can see how ugly/dated they look. I'd like a fresh modern corporate look.

Target Market(s)

These are for our clients, potential clients, industry contacts - like all business cards

Contact Information for Business Card

Name
Position
Company Address - Level 1, 47 Fernby Street, Carlow Qld 4072
Direct Phone
mobile
Email
Website -www.korvalit.com.au
Logo

Colors

Designer to choose colors to be used in the design.

Requirements
Must have
• Main Logo
• Cards will need to be editable to be able to personalize them for each new employee.
Nice to have
• The MapOut, ShipWell, KeepSteady would be okay to have if they can be sensibly and professionally added to the look without detracting from the main imagery.
• Maybe they could go on the back of the card? will leave this to your creative discretion as to whether/where they fit.
Should not have
• Should not have decorative or script fonts

```html
<!DOCTYPE html>
<html lang="en">
<head>
<meta charset="utf-8">
<title>korvalit business card</title>
<link href="https://fonts.googleapis.com/css2?family=Roboto:wght@400;500&display=swap" rel="stylesheet">
<style>
  :root {
    --backdrop: #d8d8d8;
    --card-white: #ffffff;
    --card-black: #040608;
    --brand-blue: #2c86cf;
    --pattern-blue: #e3eef8;
    --text-light: #f2f2f2;
  }
  * { box-sizing: border-box; margin: 0; padding: 0; }
  html, body { width: 1200px; height: 800px; overflow: hidden; }
  body {
    background: var(--backdrop);
    font-family: "Roboto", Arial, sans-serif;
    position: relative;
  }
  .card {
    position: absolute;
    top: 240px;
    width: 520px;
    height: 318px;
    box-shadow: 0 3px 10px rgba(0,0,0,0.18);
    overflow: hidden;
  }
  .card-front { left: 60px; background: var(--card-black); }
  .card-back { left: 620px; background: var(--card-white); }

  .brand-strip {
    position: absolute;
    left: 0; top: 0; bottom: 0;
    width: 116px;
    background: var(--card-white);
  }
  .brand-strip .brand-name {
    position: absolute;
    left: 58px; top: 159px;
    transform: translate(-50%, -50%) rotate(-90deg);
    font-size: 38px;
    font-weight: 500;
    color: var(--brand-blue);
    letter-spacing: 0.5px;
    white-space: nowrap;
  }
  .brand-strip .brand-dot {
    position: absolute;
    left: 46px; bottom: 20px;
    width: 24px; height: 24px;
    background: var(--brand-blue);
  }

  .contact {
    position: absolute;
    left: 150px; top: 52px;
    color: var(--text-light);
  }
  .contact .person-name {
    font-size: 24px;
    font-weight: 500;
    color: var(--brand-blue);
    letter-spacing: 0.3px;
    line-height: 1;
  }
  .contact .person-role {
    font-size: 13px;
    margin-top: 4px;
  }
  .contact .address {
    font-size: 13px;
    line-height: 1.35;
    margin-top: 22px;
  }
  .contact .lines {
    list-style: none;
    margin-top: 20px;
    font-size: 13px;
    line-height: 1.5;
  }
  .contact .lines li { display: flex; align-items: center; gap: 10px; }
  .contact .lines svg { width: 10px; height: 10px; flex: none; }
  .contact .accent { color: var(--brand-blue); }

  .back-pattern {
    position: absolute; inset: 0;
    background: linear-gradient(135deg, var(--pattern-blue), #f4f8fc);
  }
  .back-brand {
    position: absolute;
    left: 50%; top: 50%;
    transform: translate(-50%, -50%);
    display: flex; align-items: center; gap: 10px;
    background: var(--card-white);
    padding: 8px 14px;
  }
  .back-brand .brand-dot {
    width: 22px; height: 22px; background: var(--brand-blue);
  }
  .back-brand .brand-name {
    font-size: 30px; font-weight: 500; color: var(--brand-blue);
  }
</style>
</head>
<body>

<section class="card card-front">
  <div class="brand-strip">
    <span class="brand-name">korvalit</span>
    <span class="brand-dot"></span>
  </div>

  <div class="contact">
    <p class="person-name">MARA DELLING</p>
    <p class="person-role">Business Development Manager</p>
    <p class="address">22/9 Ashcombe Road,<br>Renwick QLD 4019</p>
    <ul class="lines">
      <li>
        <svg viewBox="0 0 10 10"><rect x="2.5" y="0.5" width="5" height="9" rx="1" fill="none" stroke="#2c86cf" stroke-width="1.2"/></svg>
        +61 (0)412 555 018
      </li>
      <li>
        <svg viewBox="0 0 10 10"><path d="M2 1 L4 1 L4.6 3 L3.4 4 Q4.5 6 6 6.6 L7 5.4 L9 6 L9 8 Q5 9 1 3 Z" fill="#2c86cf"/></svg>
        +61 (0)7 3555 0142
      </li>
      <li>
        <svg viewBox="0 0 10 10"><path d="M2 1 L4 1 L4.6 3 L3.4 4 Q4.5 6 6 6.6 L7 5.4 L9 6 L9 8 Q5 9 1 3 Z" fill="#2c86cf"/></svg>
        +61 (0)7 3555 0150
      </li>
      <li>
        <svg viewBox="0 0 10 10"><rect x="1" y="3" width="8" height="6" fill="#2c86cf"/><rect x="3" y="1" width="4" height="2" fill="#2c86cf"/></svg>
        +61 (0)7 3555 0163
      </li>
      <li>
        <svg viewBox="0 0 10 10"><rect x="0.6" y="2" width="8.8" height="6" fill="none" stroke="#2c86cf" stroke-width="1.2"/><path d="M0.6 2 L5 5.5 L9.4 2" fill="none" stroke="#2c86cf" stroke-width="1.2"/></svg>
        mdelling@korvalit.com.au
      </li>
      <li>
        <svg viewBox="0 0 10 10"><circle cx="5" cy="5" r="4.3" fill="none" stroke="#2c86cf" stroke-width="1.2"/><path d="M0.7 5 H9.3 M5 0.7 Q2 5 5 9.3 M5 0.7 Q8 5 5 9.3" fill="none" stroke="#2c86cf" stroke-width="0.9"/></svg>
        <span>www.<span class="accent">korvalit</span>.com.au</span>
      </li>
    </ul>
  </div>
</section>

<section class="card card-back">
  <div class="back-pattern" role="img" aria-label="Soft repeating brand pattern in pale blue"></div>
  <div class="back-brand">
    <span class="brand-dot"></span>
    <span class="brand-name">korvalit</span>
  </div>
</section>

</body>
</html>
```